graphic showing our process of education as a process called a pipeline

Also see my updated comments on discussion section.
Title of the graphic needs to be:
TITLE = The KESIMA Strategic Leadership Pipeline = larger, bold heading
SUB-TITLE = Developing a steady flow of servant leaders for Tanzania's future = under title; smaller font
change the text for each of the 7 steps to match the outcomes listed on the newly attached PDF (strategic pipeline 11x17)
Pipe should be straight or mostly straight.
Pipe should not be in a strong or dark color.
Any icons or symbols should be simple and professional, not like cartoon or childish.
We need a graphic design that shows our PROCESS, called a "pipeline," that is creating future leaders. We are a US-based non-profit that operates a Christian school in rural Tanzania for 600 students (pre-K through 12th grade). It starts with child sponsorship program that allows poor children and orphans to attend school, we have a primary school (like USA elementary school, pre-K thru 7th), and are building a secondary boarding school (like USA middle and high school, grades 8-12), where students will live on campus in dormitories. We offer education, scholarships, leadership development experiences, help finding and securing college scholarships, academic and career counseling, placements for internships and jobs, and networking and leadership development content and events to create the next generation of servant leaders for the country. Prominent colors should probably be the green, blue and black in the Tanzania flag; we want the design to communicate "smart" and "strategic." The stages of the pipeline need to be properly named; we need to show a "leak" in the pipeline after the primary school because we currently have to send our students AWAY to other boarding schools because we don't have one. As the attached recording says, this is bad for their progress. The attached pipeline graphic is very rough and NOT meant to be imitated. It is factually correct, but is busy and not attractive.

Target Market(s)

Major financial contributors and foundations that want to give money to the cause

Industry/Entity Type

non-profit/Christian ministry in education

Font styles to use
Sans Serif

Requirements
Must have
• A "smart" and strategic" feel; preferably visible when on a half page
Nice to have
• a smart, sophisticated, serious look and feel
Should not have
• an elementary school feel

```html
<!DOCTYPE html>
<html lang="en">
<head>
<meta charset="utf-8">
<title>The KESIMA Strategic Leadership Pipeline</title>
<link rel="stylesheet" href="https://fonts.googleapis.com/css2?family=Catamaran:wght@300;400;600;700;800&family=Open+Sans:wght@300;400&display=swap">
<style>
  :root{
    --canvas:#ffffff;
    --panel:#c4e9f0;
    --green:#3cb843;
    --ink:#111111;
    --muted:#7a7a7a;
    --card:#ffffff;
    --pipe-top:#a3a9ab;
    --pipe-bottom:#8b9396;
    --joint:#d6d8d9;
    --drop:#4ccfe6;
  }
  *{box-sizing:border-box;margin:0;padding:0}
  html,body{width:1200px;height:1200px;overflow:hidden;background:var(--canvas)}
  .canvas{position:relative;width:1200px;height:1200px}
  .panel{position:absolute;left:93px;top:273px;width:1021px;height:661px;background:var(--panel);overflow:hidden}
  .footer-band{position:absolute;left:0;bottom:0;width:100%;height:26px;background:var(--green)}
  .title{position:absolute;left:0;width:100%;top:36px;text-align:center;font-family:"Catamaran",sans-serif;font-weight:700;font-size:50px;line-height:1;color:var(--ink);letter-spacing:-0.3px}
  .subtitle{position:absolute;left:0;width:100%;top:93px;text-align:center;font-family:"Catamaran",sans-serif;font-weight:300;font-size:28px;line-height:1;color:var(--ink)}
  .stage{position:absolute;background:var(--card);border-radius:10px 0 0 10px;padding:0 10px}
  .stage-name{font-family:"Catamaran",sans-serif;font-weight:600;font-size:14px;line-height:16.5px;color:var(--ink)}
  .stage-outcome{margin-top:6px;font-family:"Open Sans",sans-serif;font-weight:300;font-size:9.4px;line-height:11.6px;color:var(--muted)}
  .stage-icon{position:absolute;background:var(--green);border-radius:10px;opacity:.9}
  .pipeline{position:absolute;left:0;top:0;width:1021px;height:661px}
  .brand{position:absolute;left:33px;top:563px;width:163px;height:43px;background:#fff;display:flex;align-items:center;justify-content:center;gap:8px;font-family:"Catamaran",sans-serif;font-weight:800;font-size:30px;letter-spacing:1px;color:var(--green)}
  .brand-dot{width:14px;height:14px;border-radius:50%;background:var(--green)}
  .children{position:absolute;left:91px;top:352px;width:52px;height:60px;background:var(--green);border-radius:14px;opacity:.9}
</style>
</head>
<body>
<div class="canvas">
  <section class="panel">
    <h1 class="title">The KESIMA Strategic Leadership Pipeline</h1>
    <p class="subtitle">Developing a steady flow of servant leaders for Tanzania's future</p>

    <svg class="pipeline" viewBox="0 0 1021 661" aria-hidden="true">
      <defs>
        <linearGradient id="pipeBody" x1="0" y1="0" x2="0" y2="1">
          <stop offset="0" stop-color="#a9aeb0"/>
          <stop offset="0.8" stop-color="#9aa1a3"/>
          <stop offset="0.82" stop-color="#858d90"/>
          <stop offset="1" stop-color="#858d90"/>
        </linearGradient>
        <linearGradient id="joint" x1="0" y1="0" x2="1" y2="0">
          <stop offset="0" stop-color="#b9bcbd"/>
          <stop offset="0.5" stop-color="#e4e5e6"/>
          <stop offset="1" stop-color="#b9bcbd"/>
        </linearGradient>
        <filter id="blur"><feGaussianBlur stdDeviation="14"/></filter>
      </defs>
      <ellipse cx="512" cy="432" rx="330" ry="20" fill="#6fa3b2" opacity=".55" filter="url(#blur)"/>
      <rect x="176" y="375" width="673" height="34" fill="url(#pipeBody)"/>
      <rect x="176" y="373" width="15" height="38" fill="url(#joint)"/>
      <rect x="834" y="373" width="15" height="38" fill="url(#joint)"/>
      <g fill="url(#joint)">
        <rect x="292" y="373" width="10" height="38" rx="2"/>
        <rect x="400" y="373" width="10" height="38" rx="2"/>
        <rect x="509" y="373" width="10" height="38" rx="2"/>
        <rect x="618" y="373" width="10" height="38" rx="2"/>
        <rect x="727" y="373" width="10" height="38" rx="2"/>
      </g>
      <g stroke="#222" stroke-width="1" stroke-dasharray="5 4" fill="none">
        <path d="M119 278 V345"/>
        <path d="M298 335 V368"/>
        <path d="M513 327 V368"/>
        <path d="M731 330 V368"/>
        <path d="M396 391 H383 V464"/>
        <path d="M623 421 V471"/>
        <path d="M843 421 V460"/>
      </g>
      <g fill="#111">
        <circle cx="119" cy="345" r="2.4"/>
        <circle cx="298" cy="368" r="2.4"/>
        <circle cx="513" cy="368" r="2.4"/>
        <circle cx="731" cy="368" r="2.4"/>
        <circle cx="396" cy="391" r="2.4"/>
        <circle cx="623" cy="421" r="2.4"/>
        <circle cx="843" cy="421" r="2.4"/>
      </g>
      <g fill="var(--drop)">
        <path d="M404 415 q-5 7 -5 10 a5 5 0 0 0 10 0 q0 -3 -5 -10z"/>
        <path d="M404 430 q-7 10 -7 14 a7 7 0 0 0 14 0 q0 -4 -7 -14z"/>
      </g>
    </svg>

    <div class="children" role="img" aria-label="Simple icon of two children"></div>

    <article class="stage" style="left:73px;top:166px;width:110px;height:112px;padding-top:13px">
      <h2 class="stage-name">KESIMA<br>Sponsorship<br>Project</h2>
      <p class="stage-outcome">Close early<br>development gap</p>
    </article>

    <article class="stage" style="left:247px;top:170px;width:151px;height:165px;padding-top:39px">
      <div class="stage-icon" role="img" aria-label="Icon of a row of young students" style="left:56px;top:18px;width:85px;height:30px"></div>
      <h2 class="stage-name">Kesima<br>Leadership Primary<br>School - (Mlimani)</h2>
      <p class="stage-outcome">Potential leaders with<br>Biblical worldview and<br>strong academic<br>foundations.</p>
    </article>

    <article class="stage" style="left:466px;top:173px;width:147px;height:154px;padding-top:36px">
      <div class="stage-icon" role="img" aria-label="Icon of a group of people with stars" style="left:78px;top:11px;width:48px;height:36px"></div>
      <h2 class="stage-name">Kesima<br>Service Leadership<br>Experience</h2>
      <p class="stage-outcome">Growing servant<br>leaders with practical<br>experience to effect<br>change for the Kingdom.</p>
    </article>

    <article class="stage" style="left:676px;top:175px;width:135px;height:155px;padding-top:35px">
      <div class="stage-icon" role="img" aria-label="Icon of three professionals" style="left:67px;top:17px;width:55px;height:28px"></div>
      <h2 class="stage-name">Kesima<br>Employment<br>Center</h2>
      <p class="stage-outcome">Capable Christcentered<br>leaders in the marketplace,<br>as value adding employees<br>and entrepreneurs.</p>
    </article>

    <article class="stage" style="left:337px;top:464px;width:160px;height:141px;padding-top:37px">
      <div class="stage-icon" role="img" aria-label="Icon of a row of older students" style="left:57px;top:14px;width:95px;height:30px"></div>
      <h2 class="stage-name">Kesima<br>Leadership Secondary<br>School - (Mlimani)</h2>
      <p class="stage-outcome">Emerging leaders with<br>concrete skills and strong<br>servant mindset.</p>
    </article>

    <article class="stage" style="left:555px;top:475px;width:171px;height:132px;padding-top:35px">
      <div class="stage-icon" role="img" aria-label="Icon of three graduates in caps" style="left:77px;top:9px;width:61px;height:31px"></div>
      <h2 class="stage-name">Kesima<br>Higher Education Support</h2>
      <p class="stage-outcome">Expanding vision, capability,<br>and motivation to solve bigger<br>challenges for the nation.</p>
    </article>

    <article class="stage" style="left:781px;top:462px;width:160px;height:145px;padding-top:48px">
      <div class="stage-icon" role="img" aria-label="Icon of a group of leaders" style="left:95px;top:9px;width:53px;height:48px"></div>
      <h2 class="stage-name">Kesima<br>Leadership Hub</h2>
      <p class="stage-outcome">Mature Christian leaders being<br>placed and positioned for<br>leadership roles in the community<br>and nation.</p>
    </article>

    <div class="brand"><span class="brand-dot"></span>KESIMA</div>

    <div class="footer-band"></div>
  </section>
</div>
</body>
</html>
```